Classy, Elegant, Simple Business Card Design

Looking to have a classy, simple, and elegant design. Want a top notch designed business card. I really like the look of the new torvane credit card. I also like the design I attached. I am trying to reach 21-29 year old females for booking us for there wedding or event. We offer Disc Jockey Service, Photo Booth Rentals, and Uplighting .

Target Market(s)

21-28 year old females

Contact Information for Business Card

Has to have logo, website, email, and phone number

Font styles to use
Other font styles liked:
• open to font choice, modern, clean
Designer to choose
33a6d7
0791cd
0555a3
ffffff

Requirements
Must have
• Has to have logo, website, email, and phone number
Nice to have
• I really like the design of the new torvane credit card. I also included my logo and some designs I like
Should not have
• clutter or too much info

```html
<!DOCTYPE html>
<html lang="en">
<head>
<meta charset="utf-8">
<title>Velmoraine Event Group – Business Card</title>
<link href="https://fonts.googleapis.com/css2?family=Work+Sans:wght@400;500;600&display=swap" rel="stylesheet">
<style>
  :root {
    --bg: #1c1c1d;
    --card: #262627;
    --card-edge: #2f2f30;
    --white: #ffffff;
    --silver: #b9babc;
    --sky: #33a6d7;
    --blue: #0791cd;
    --navy: #0555a3;
  }
  * { margin: 0; padding: 0; box-sizing: border-box; }
  html, body { width: 1200px; height: 900px; overflow: hidden; }
  body {
    background: var(--bg);
    font-family: "Work Sans", Arial, sans-serif;
    position: relative;
  }
  .card {
    position: absolute;
    left: 270px;
    width: 660px;
    height: 377px;
    background: linear-gradient(160deg, var(--card-edge) 0%, var(--card) 60%);
    overflow: hidden;
  }
  .card--back { top: 53px; }
  .card--front { top: 470px; }

  .wordmark {
    position: absolute;
    display: flex;
    flex-direction: column;
    align-items: center;
    justify-content: center;
    font-weight: 500;
  }
  .wordmark__dot {
    width: 40px; height: 40px; border-radius: 50%;
    background: currentColor;
    margin-bottom: 18px;
  }
  .wordmark__name { line-height: 1; white-space: nowrap; }
  .wordmark__sub { white-space: nowrap; margin-top: 10px; }

  /* back */
  .card--back .wordmark { inset: 0; color: var(--silver); }
  .card--back .wordmark__name { font-size: 40px; letter-spacing: 4px; }
  .card--back .wordmark__sub { font-size: 15px; letter-spacing: 10px; padding-left: 10px; }

  /* front */
  .card--front .wordmark {
    left: 30px; top: 0; width: 320px; height: 100%;
    color: var(--white);
  }
  .card--front .wordmark__name { font-size: 34px; letter-spacing: 3px; }
  .card--front .wordmark__sub { font-size: 13px; letter-spacing: 9px; padding-left: 9px; }

  .divider {
    position: absolute;
    left: 362px; top: 72px;
    width: 2px; height: 233px;
    background: var(--blue);
  }
  .contact {
    position: absolute;
    left: 392px; top: 84px;
    width: 250px;
    color: var(--white);
  }
  .contact__name {
    color: var(--blue);
    font-weight: 600;
    font-size: 25px;
    letter-spacing: 1px;
    line-height: 1.1;
    white-space: nowrap;
  }
  .contact__role { font-size: 16px; letter-spacing: 1px; margin-top: 4px; }
  .contact__address { font-size: 16px; letter-spacing: 1px; line-height: 1.45; margin-top: 16px; white-space: nowrap; }
  .contact__list { list-style: none; margin-top: 14px; font-size: 16px; letter-spacing: 1px; }
  .contact__list li { display: flex; align-items: center; gap: 10px; line-height: 1.6; white-space: nowrap; }
  .contact__list svg { width: 12px; height: 12px; flex: none; }
  .accent { color: var(--blue); }
</style>
</head>
<body>
  <section class="card card--back" aria-label="Card back">
    <div class="wordmark">
      <span class="wordmark__dot"></span>
      <span class="wordmark__name">VELMORAINE</span>
      <span class="wordmark__sub">EVENT GROUP</span>
    </div>
  </section>

  <section class="card card--front" aria-label="Card front">
    <div class="wordmark">
      <span class="wordmark__dot"></span>
      <span class="wordmark__name">VELMORAINE</span>
      <span class="wordmark__sub">EVENT GROUP</span>
    </div>
    <div class="divider"></div>
    <div class="contact">
      <h1 class="contact__name">DANIEL REYES</h1>
      <p class="contact__role">Managing Partner</p>
      <p class="contact__address">418 Harbor Crest Ave.,<br>Los Angeles, CA 90012</p>
      <ul class="contact__list">
        <li>
          <svg viewBox="0 0 12 12" fill="none" stroke="#0791cd" stroke-width="1.2"><path d="M3 1 L5 3.5 L4 5 Q5.5 7.5 7 8 L8.5 7 L11 9 L9.5 11 Q4 10.5 1 3 Z"/></svg>
          615-555-0148
        </li>
        <li>
          <svg viewBox="0 0 12 12" fill="none" stroke="#0791cd" stroke-width="1.2"><rect x="1" y="2.5" width="10" height="7"/><path d="M1 2.5 L6 6.5 L11 2.5"/></svg>
          info@velmoraine.com
        </li>
        <li>
          <svg viewBox="0 0 12 12" fill="none" stroke="#0791cd" stroke-width="1"><circle cx="6" cy="6" r="5"/><ellipse cx="6" cy="6" rx="2.2" ry="5"/><path d="M1 6 H11 M2 3.5 H10 M2 8.5 H10"/></svg>
          <span>www.<span class="accent">velmoraine</span>.com</span>
        </li>
      </ul>
    </div>
  </section>
</body>
</html>
```